Business Card Design needed for start up company Halvora

In need of a new business card designed for a start up company based in Sydney, Halvora is a new start up innovative Company, our mission it to make property accessible for everyday Australian and to become the leading Real Estate platform in Australia. We want it to be fresh and clean.

Industry/Entity Type

Financial

Contact Information for Business Card

Section for Name
Section for Title

HALVORA - The Strength of Pooling
Mobile:
Direct:

Font styles to use
Sans Serif

Colors
33a6d7
0692cd
0255a3
ffffff

Requirements
Must have
• Logo, all business card details

```html
<!DOCTYPE html>
<html lang="en">
<head>
<meta charset="utf-8">
<title>Halvora Business Card</title>
<link href="https://fonts.googleapis.com/css2?family=Roboto:wght@400;500;900&display=swap" rel="stylesheet">
<style>
  :root{
    --sky:#239bd6;
    --sky-deep:#0692cd;
    --navy:#1f4a85;
    --ink:#2b2f36;
    --paper:#ffffff;
    --stage:#5e666b;
  }
  *{margin:0;padding:0;box-sizing:border-box}
  html,body{width:1200px;height:900px;overflow:hidden}
  body{
    background:var(--stage);
    font-family:"Roboto",Arial,sans-serif;
    position:relative;
  }
  .card{
    position:absolute;
    top:295px;
    width:540px;height:310px;
    border-radius:16px;
    overflow:hidden;
    box-shadow:0 10px 24px rgba(0,0,0,.35);
  }
  .card--front{left:40px;background:var(--sky)}
  .card--back{left:620px;background:var(--paper)}

  /* front */
  .front-brand{
    position:absolute;left:50%;top:50%;
    transform:translate(-50%,-50%);
    display:flex;align-items:center;gap:14px;
  }
  .brand-dot{width:74px;height:74px;border-radius:50%;background:var(--paper)}
  .brand-name{
    font-weight:900;color:var(--navy);
    font-size:64px;letter-spacing:1px;line-height:1;
  }

  /* back */
  .back-shapes{position:absolute;inset:0}
  .back-brand{
    position:absolute;left:34px;top:30px;
    display:flex;align-items:center;gap:8px;
  }
  .back-brand .brand-dot{width:40px;height:40px;background:var(--sky)}
  .back-brand .brand-name{font-size:34px}

  .contact-list{
    position:absolute;left:34px;top:118px;
    list-style:none;
  }
  .contact-item{
    display:flex;align-items:center;gap:8px;
    font-size:13px;color:var(--ink);
    height:24px;
  }
  .contact-icon{
    width:16px;height:16px;border-radius:2px;
    background:var(--navy);
    display:flex;align-items:center;justify-content:center;
  }
  .contact-icon svg{width:11px;height:11px}

  .holder{
    position:absolute;right:26px;top:55px;
    width:180px;height:40px;
    text-align:center;color:var(--paper);
    display:flex;flex-direction:column;justify-content:center;
  }
  .holder-name{font-size:17px;font-weight:400;letter-spacing:1px;line-height:1.1}
  .holder-title{font-size:9px;letter-spacing:.5px;margin-top:2px}

  .address{
    position:absolute;right:36px;bottom:46px;
    color:var(--paper);font-size:13px;line-height:1.45;
    text-align:left;width:220px;
  }
</style>
</head>
<body>

<section class="card card--front" aria-label="Card front">
  <div class="front-brand">
    <span class="brand-dot"></span>
    <span class="brand-name">HALVORA</span>
  </div>
</section>

<section class="card card--back" aria-label="Card back">
  <svg class="back-shapes" viewBox="0 0 540 310" width="540" height="310" aria-hidden="true">
    <polygon points="185,310 395,0 540,0 540,310" fill="#1f4a85"/>
    <polygon points="318,98 344,55 540,55 540,98" fill="#239bd6"/>
    <polygon points="344,55 370,42 376,55" fill="#0692cd"/>
  </svg>

  <div class="back-brand">
    <span class="brand-dot"></span>
    <span class="brand-name">HALVORA</span>
  </div>

  <ul class="contact-list">
    <li class="contact-item">
      <span class="contact-icon"><svg viewBox="0 0 12 12"><path d="M2.5 1l2 2-1 1.2a6 6 0 0 0 3.3 3.3L8 6.5l2 2-1.3 1.6C5 10 2 7 1.9 3.3z" fill="#fff"/></svg></span>
      <span>02-8470-3316</span>
    </li>
    <li class="contact-item">
      <span class="contact-icon"><svg viewBox="0 0 12 12"><rect x="3.5" y="1" width="5" height="10" rx="1" fill="none" stroke="#fff" stroke-width="1.2"/></svg></span>
      <span>0412-558-207</span>
    </li>
    <li class="contact-item">
      <span class="contact-icon"><svg viewBox="0 0 12 12"><rect x="1.5" y="3" width="9" height="6" fill="none" stroke="#fff" stroke-width="1.1"/><path d="M1.5 3l4.5 3.5L10.5 3" fill="none" stroke="#fff" stroke-width="1.1"/></svg></span>
      <span>mara@halvora.au</span>
    </li>
    <li class="contact-item">
      <span class="contact-icon"><svg viewBox="0 0 12 12"><circle cx="6" cy="6" r="4.3" fill="none" stroke="#fff" stroke-width="1.1"/><path d="M1.7 6h8.6M6 1.7c-2 2.5-2 6.1 0 8.6M6 1.7c2 2.5 2 6.1 0 8.6" fill="none" stroke="#fff" stroke-width=".9"/></svg></span>
      <span>www.halvoraproperty.au</span>
    </li>
  </ul>

  <div class="holder">
    <span class="holder-name">MARA ELLISON</span>
    <span class="holder-title">OWNER</span>
  </div>

  <p class="address">48 Kellerton Lane, Level 7<br>Sydney, NSW 2000</p>
</section>

</body>
</html>
```